Brookvane Consulting Business Card Design

Business Card Design for Brookvane Consulting. Brookvane Consulting is a boutique consultancy based in Atlanta, GA., that specializes in marketing strategy, organization planning, and leadership development. We provide solutions for small businesses and startups as well as Vantage 300 companies.

http://brookvaneconsulting.com/

Target Market(s)

We provide solutions for small businesses and startups as well as Vantage 300 companies.

Industry/Entity Type

Consulting

Contact Information for Business Card

Two sided business card with priority on contact information, logo, tag line (Inspiration to Dream More, Do More, Become More)

Colors

Designer to choose colors to be used in the design.

Requirements
Must have
• contact information, logo, tag line (Inspiration to Dream More, Do More, Become More)
• Simple no over communication.
Nice to have
• I would like to see different placements of logo and creative use of both sides of the card
Should not have
• Do not put too much information on the card.

```html
<!DOCTYPE html>
<html lang="en">
<head>
<meta charset="utf-8">
<title>Brookvane Consulting – Business Card</title>
<link href="https://fonts.googleapis.com/css2?family=Montserrat:wght@600&family=Roboto:wght@400&family=Lobster+Two:ital,wght@1,700&display=swap" rel="stylesheet">
<style>
  :root {
    --backdrop: #3a3a3a;
    --card: #333333;
    --band: #0b0b0b;
    --strip: #bdbdbd;
    --ink: #ffffff;
  }
  * { margin: 0; padding: 0; box-sizing: border-box; }
  html, body { width: 799px; height: 1200px; overflow: hidden; }
  body {
    background: var(--backdrop);
    position: relative;
    font-family: "Roboto", Arial, sans-serif;
    color: var(--ink);
  }
  .card {
    position: absolute;
    left: 90px;
    width: 620px;
    height: 354px;
    background: var(--card);
    border-radius: 30px;
    overflow: hidden;
    box-shadow: 0 14px 30px rgba(0,0,0,0.45);
  }
  .card--front { top: 150px; }
  .card--back { top: 690px; }

  .wordmark {
    position: absolute;
    display: flex;
    align-items: center;
    gap: 14px;
    font-family: "Montserrat", Arial, sans-serif;
    font-weight: 600;
    color: var(--ink);
    white-space: nowrap;
  }
  .wordmark__square {
    width: 22px; height: 22px;
    background: var(--ink);
    flex: none;
  }
  .card--front .wordmark {
    left: 0; right: 0; top: 150px;
    justify-content: center;
    font-size: 38px;
  }
  .card--back .wordmark {
    left: 40px; top: 48px;
    font-size: 30px;
  }

  .holder-name {
    position: absolute;
    left: 40px; top: 150px;
    font-family: "Lobster Two", cursive;
    font-style: italic;
    font-weight: 700;
    font-size: 22px;
  }
  .contact {
    position: absolute;
    right: 40px; top: 180px;
    list-style: none;
    font-size: 16px;
    line-height: 22px;
  }
  .footer-band {
    position: absolute;
    left: 0; right: 0; bottom: 0;
    height: 90px;
  }
  .footer-band svg { position: absolute; inset: 0; }
  .tagline {
    position: absolute;
    right: 40px; bottom: 34px;
    font-size: 15px;
    letter-spacing: 0.2px;
  }
</style>
</head>
<body>
  <section class="card card--front" aria-label="Card front">
    <div class="wordmark"><span class="wordmark__square"></span>Brookvane Consulting</div>
  </section>

  <section class="card card--back" aria-label="Card back">
    <div class="wordmark"><span class="wordmark__square"></span>Brookvane Consulting</div>
    <p class="holder-name">Darnell</p>
    <ul class="contact">
      <li>555-010-4827</li>
      <li>darnell@brookvaneconsulting.com</li>
      <li>www.brookvaneconsulting.com</li>
    </ul>
    <div class="footer-band">
      <svg width="620" height="90" viewBox="0 0 620 90" preserveAspectRatio="none">
        <polygon points="0,0 250,0 210,90 0,90" fill="var(--strip)"/>
        <polygon points="250,0 620,0 620,90 210,90" fill="var(--band)"/>
        <polygon points="0,0 250,0 246,8 0,8" fill="#e6e6e6"/>
      </svg>
      <p class="tagline">Inspiration to Dream More, Do More, Become More</p>
    </div>
  </section>
</body>
</html>
```